You are cordially invited to attend a delicious Afternoon Tea at The Ashcombe.

Enjoy a glass of sparkling wine whilst afternoon delicacies and a menu of fine teas is presented for you to enjoy throughout the afternoon.

This is an opportunity to get together with a table of like minded ladies just for fun and to share some stories and meet some new friends.

Date: 8 August 2014
Time: 12pm - 2pm
Venue: 47 Larkfield Street, Melbourne VIC 3000

(hello please see above text we require - we would like to invite our clients to an afternoon tea, an invitation (hard copy) to be of elegant taste, nice lettering, pic added to the invite).

```html
<!DOCTYPE html>
<html lang="en">
<head>
<meta charset="utf-8">
<title>Afternoon Tea Invitation</title>
<link rel="stylesheet" href="https://fonts.googleapis.com/css2?family=Federo&family=Josefin+Sans:wght@300;400&display=swap">
<style>
  :root {
    --page-bg: #d9d9d9;
    --card-brown: #2b1d0b;
    --card-deep: #1f1507;
    --glow-amber: #d9801f;
    --glow-orange: #b8520f;
    --text-cream: #eadcc4;
    --text-accent: #e2783a;
    --title-top: #f6a542;
    --title-bottom: #e8542c;
    --room-warm: #c9702a;
    --room-light: #e9c79a;
    --room-dark: #6a3410;
  }
  html, body {
    margin: 0;
    width: 1200px;
    height: 1000px;
    overflow: hidden;
    background: var(--page-bg);
  }
  .invitation-card {
    position: absolute;
    left: 50px;
    top: 142px;
    width: 1100px;
    height: 715px;
    overflow: hidden;
    background: linear-gradient(180deg, var(--card-brown) 0%, var(--card-deep) 100%);
    box-shadow: 0 6px 18px rgba(0,0,0,0.35);
    font-family: "Josefin Sans", sans-serif;
    font-weight: 300;
    color: var(--text-cream);
  }
  .wine-photo {
    position: absolute;
    left: 0;
    top: 0;
    width: 640px;
    height: 715px;
    background:
      radial-gradient(ellipse 55% 70% at 38% 55%, var(--glow-amber) 0%, var(--glow-orange) 40%, rgba(43,29,11,0) 100%);
  }
  .title {
    position: absolute;
    left: 673px;
    top: 60px;
    transform: translateX(-50%);
    margin: 0;
    font-family: "Federo", sans-serif;
    font-weight: 400;
    font-size: 70px;
    letter-spacing: 4px;
    line-height: 1;
    background: linear-gradient(180deg, var(--title-top), var(--title-bottom));
    -webkit-background-clip: text;
    background-clip: text;
    color: transparent;
    white-space: nowrap;
  }
  .line {
    position: absolute;
    left: 673px;
    transform: translateX(-50%);
    margin: 0;
    white-space: nowrap;
    line-height: 1;
  }
  .line--lead { font-size: 21px; }
  .line--body { font-size: 15.5px; }
  .accent { color: var(--text-accent); }
  .details {
    position: absolute;
    left: 380px;
    top: 416px;
    width: 590px;
    display: flex;
    justify-content: space-between;
    font-size: 15.5px;
    white-space: nowrap;
  }
  .tea-room-photo {
    position: absolute;
    left: 299px;
    top: 457px;
    width: 801px;
    height: 258px;
    border-top-left-radius: 34px;
    background:
      radial-gradient(ellipse 35% 60% at 50% 80%, var(--room-light) 0%, rgba(233,199,154,0) 100%),
      linear-gradient(90deg, var(--room-warm) 0%, var(--room-dark) 25%, var(--room-warm) 50%, var(--room-dark) 75%, var(--room-warm) 100%);
  }
</style>
</head>
<body>
  <main class="invitation-card">
    <div class="wine-photo" role="img" aria-label="Photograph of a wine bottle and a glass of white wine against a warm amber glow"></div>

    <h1 class="title">INVITATION</h1>

    <p class="line line--lead" style="top:166px">You are cordially invited</p>
    <p class="line line--lead" style="top:196px">to attend a delicious <span class="accent">Afternoon Tea at The Ashcombe.</span></p>

    <p class="line line--body" style="top:258px">Enjoy a glass of sparkling wine whilst <span class="accent">afternoon delicacies</span></p>
    <p class="line line--body" style="top:285px">and a menu of fine teas is presented for you to enjoy <span class="accent">throughout the afternoon.</span></p>

    <p class="line line--body" style="top:335px">This is an opportunity to get together</p>
    <p class="line line--body" style="top:362px">with a table of like minded ladies just for fun and to <span class="accent">share some stories and meet some new friends.</span></p>

    <div class="details">
      <span class="details__date">Date: 8 August 2014</span>
      <span class="details__time">Time: 12pm - 2pm</span>
      <span class="details__venue">Venue: 47 Larkfield Street, Melbourne VIC 3000</span>
    </div>

    <div class="tea-room-photo" role="img" aria-label="Photograph of an elegant tea room table set with a tiered stand of cakes, teacups and champagne glasses"></div>
  </main>
</body>
</html>
```